Business Card Design

We need a business card designed for our new company. Prefer a black card with white logo & writing.

Contact Information for Business Card

Ted Galloway, address: 7-4812 Fernhollow Road, Abbotsford, BC, V3K 8R2, Office Phone: 604-712-3390, Cell: 604-947-2164, Email: ted@resinworkshub.ca

Colors

Designer to choose only greyscale colors for use in the design.

```html
<!DOCTYPE html>
<html lang="en">
<head>
<meta charset="utf-8">
<title>Resinworks Hub – Business Card</title>
<link rel="stylesheet" href="https://fonts.googleapis.com/css2?family=Poppins:wght@300;400;600;700&display=swap">
<style>
  :root {
    --backdrop: #3b3b3d;
    --card: #1f1f21;
    --ink: #ffffff;
    --ink-soft: #d9d9d9;
    --rule: #8a8a8a;
    --emboss-edge: #4a4a4d;
  }
  * { margin: 0; padding: 0; box-sizing: border-box; }
  html, body { width: 1200px; height: 780px; overflow: hidden; }
  body {
    background: var(--backdrop);
    font-family: "Poppins", sans-serif;
    color: var(--ink);
    display: flex;
    align-items: center;
    justify-content: center;
    gap: 40px;
  }
  .card {
    position: relative;
    width: 540px;
    height: 309px;
    background: var(--card);
    border-radius: 4px;
    box-shadow: 0 10px 28px rgba(0,0,0,0.45);
    overflow: hidden;
  }

  /* Contact side */
  .brand-name {
    position: absolute;
    left: 36px;
    top: 82px;
    width: 200px;
    font-weight: 700;
    font-size: 28px;
    line-height: 1.1;
    text-transform: uppercase;
    color: var(--ink);
  }
  .divider {
    position: absolute;
    left: 232px;
    top: 70px;
    width: 60px;
    height: 150px;
  }
  .person {
    position: absolute;
    left: 302px;
    top: 74px;
  }
  .person-name {
    font-size: 28px;
    line-height: 1.1;
    font-weight: 300;
    white-space: nowrap;
  }
  .person-name .first { font-weight: 700; }
  .person-title {
    font-size: 13px;
    font-weight: 400;
    color: var(--ink-soft);
    margin-top: 2px;
  }
  .contact-list {
    list-style: none;
    margin-top: 12px;
  }
  .contact-list li {
    display: flex;
    align-items: center;
    gap: 8px;
    font-size: 13px;
    line-height: 20px;
    font-weight: 300;
    white-space: nowrap;
  }
  .contact-list svg { width: 12px; height: 12px; flex: none; }
  .address {
    position: absolute;
    left: 36px;
    bottom: 28px;
    font-size: 13px;
    font-weight: 400;
    letter-spacing: 0.2px;
  }

  /* Brand side */
  .card--front {
    display: flex;
    align-items: center;
    justify-content: center;
  }
  .front-name {
    font-weight: 700;
    font-size: 44px;
    text-transform: uppercase;
    color: var(--emboss-edge);
    letter-spacing: 1px;
  }
</style>
</head>
<body>

  <section class="card card--contact">
    <div class="brand-name">Resinworks Hub</div>

    <svg class="divider" viewBox="0 0 60 150" aria-hidden="true">
      <line x1="58" y1="2" x2="2" y2="148" stroke="var(--rule)" stroke-width="1"/>
    </svg>

    <div class="person">
      <h1 class="person-name"><span class="first">Ted</span> Galloway</h1>
      <p class="person-title">Founder &amp; CEO</p>
      <ul class="contact-list">
        <li>
          <svg viewBox="0 0 12 12" aria-hidden="true"><path d="M2.5 1h2l1 3-1.3.8a6 6 0 0 0 3 3L8 6.5l3 1v2a1.5 1.5 0 0 1-1.5 1.5A8.5 8.5 0 0 1 1 2.5 1.5 1.5 0 0 1 2.5 1z" fill="var(--ink)"/></svg>
          604-712-3390
        </li>
        <li>
          <svg viewBox="0 0 12 12" aria-hidden="true"><rect x="3" y="0.5" width="6" height="11" rx="1" fill="none" stroke="var(--ink)" stroke-width="1.2"/><circle cx="6" cy="9.5" r="0.7" fill="var(--ink)"/></svg>
          604-947-2164
        </li>
        <li>
          <svg viewBox="0 0 12 12" aria-hidden="true"><circle cx="6" cy="6" r="5" fill="none" stroke="var(--ink)" stroke-width="1.1"/><ellipse cx="6" cy="6" rx="2.2" ry="5" fill="none" stroke="var(--ink)" stroke-width="0.9"/><line x1="1" y1="6" x2="11" y2="6" stroke="var(--ink)" stroke-width="0.9"/></svg>
          www.resinworkshub.ca
        </li>
        <li>
          <svg viewBox="0 0 12 12" aria-hidden="true"><rect x="0.6" y="2.2" width="10.8" height="7.6" rx="0.8" fill="none" stroke="var(--ink)" stroke-width="1.1"/><path d="M1 2.8 6 6.6l5-3.8" fill="none" stroke="var(--ink)" stroke-width="1.1"/></svg>
          ted@resinworkshub.ca
        </li>
      </ul>
    </div>

    <p class="address">7-4812 Fernhollow Road, Abbotsford, BC, V3K 8R2.</p>
  </section>

  <section class="card card--front">
    <div class="front-name">Resinworks Hub</div>
  </section>

</body>
</html>
```